Dultavo.com webside

I want to build a Dultavo.com retail website use on Shopify, reselling three main categories: Office Supplies, Packing Supplies, and Home Consumables. I also wish the webpage has the same functions as the Zelvik home page. The page is split into three different parts with the top being a sliding screen showcasing promotion products, below it being the three categories, and finally, a moving screen showing company missions.
Target Market(s)
U.S online
Industry/Entity Type
Office Supplies, packing Supplies and Home Consumables
Coding
Coded - Design and coding required
Number of Pages Required
5+ page
Look and feel

```html
<!DOCTYPE html>
<html lang="en">
<head>
<meta charset="utf-8">
<title>Dultavo – Office, Packing &amp; Home Supplies</title>
<link rel="stylesheet" href="https://fonts.googleapis.com/css2?family=Roboto:wght@300;400;500;700;900&display=swap">
<style>
:root{
  --green:#16a27e;
  --green-dark:#0f8a6a;
  --ink:#222;
  --muted:#777;
  --star:#f29b1d;
  --soft:#f3f4f6;
  --tile:#eceef0;
  --yellow:#ffd21f;
  --footer:#111;
}
*{box-sizing:border-box;margin:0;padding:0}
html,body{width:1200px;height:5333px;overflow:hidden;background:#fff;font-family:"Roboto",Arial,sans-serif;color:var(--ink)}
.page{position:relative;width:1200px;height:5333px}
.abs{position:absolute}

.topbar{height:50px;background:var(--green);color:#fff;font-size:16px;display:flex;align-items:center;justify-content:center}
.nav{height:111px;position:relative;border-bottom:1px solid #eee}
.menu{position:absolute;left:112px;top:44px;display:flex;gap:34px;font-size:13px;font-weight:500}
.menu a{color:var(--ink);text-decoration:none}
.menu a.active{color:var(--green);position:relative}
.menu a.active::after{content:"";position:absolute;left:0;right:0;top:30px;height:3px;background:var(--green)}
.logo{position:absolute;left:518px;top:30px;font-size:40px;font-weight:900;letter-spacing:1px;color:#1c1c1c}
.search{position:absolute;left:706px;top:85px;margin-top:-44px;width:246px;height:44px;border:1px solid #999;border-radius:22px;display:flex;align-items:center;justify-content:space-between;padding:0 16px;font-size:13px}
.cart{position:absolute;left:1028px;top:42px;font-size:13px;font-weight:500;display:flex;align-items:center;gap:4px}
.cart .count{position:absolute;left:8px;top:-10px;font-size:11px}

.hero{position:relative;height:584px;display:flex}
.hero .panel{width:400px;height:584px;position:relative}
.panel.office{background:linear-gradient(135deg,#9aa0a4,#5d6266 60%,#3d4144)}
.panel.home{background:linear-gradient(135deg,#6d5a4a,#4a3c33 60%,#2f2823);width:400px}
.panel.offer{background:var(--green);color:#fff;text-align:center}
.panel .caption{position:absolute;left:36px;top:620px;margin-top:-161px}
.caption small{font-size:14px;display:block}
.caption h3{font-size:27px;font-weight:400;margin:4px 0 6px}
.caption a{color:#fff;font-size:13px;text-decoration:underline}
.offer .art{position:absolute;left:50px;top:36px;width:300px;height:196px;border-radius:8px;background:linear-gradient(180deg,#2f3b3a,#18a07d 90%)}
.offer .lead{position:absolute;top:270px;left:0;right:0;font-size:16px}
.offer .date{position:absolute;top:290px;left:0;right:0;font-size:38px;font-weight:700;color:var(--yellow)}
.offer .line{position:absolute;left:0;right:0;font-size:29px;font-weight:500}
.offer .free{position:absolute;top:440px;left:50px;display:flex;align-items:center;gap:8px;font-size:20px;font-weight:500}
.offer .free span{font-size:13px;font-weight:400}
.offer .tiny{position:absolute;left:0;right:0;font-size:16px}
.arrow{position:absolute;top:416px;width:40px;height:40px;border-radius:50%;background:#fff;display:flex;align-items:center;justify-content:center}

.section-title{position:absolute;left:0;right:0;text-align:center;font-size:31px;font-weight:400}
.section-title::after{content:"";display:block;width:54px;height:3px;background:var(--green);margin:14px auto 0}

.grid{position:absolute;left:112px;display:grid;grid-template-columns:repeat(4,232px);column-gap:16px}
.card{text-align:center}
.card .img{height:286px;background:var(--tile);position:relative}
.card .img .fill{position:absolute;inset:40px 24px;border-radius:6px}
.badge{position:absolute;left:14px;top:14px;background:var(--green);color:#fff;font-size:12px;padding:5px 9px}
.stars{color:var(--star);font-size:13px;letter-spacing:2px;margin-top:22px}
.card h4{font-size:17px;font-weight:400;margin-top:8px}
.card .price{color:var(--green);font-size:19px;font-weight:500;margin-top:10px}

.promo{position:absolute;top:1763px;left:0;width:1200px;height:538px;background:var(--soft)}
.promo .banner{position:absolute;top:56px;width:476px;height:424px;color:#fff;text-align:center}
.banner .label{position:absolute;top:186px;left:0;right:0;font-size:15px}
.banner .label::after{content:"";display:block;width:200px;height:1px;background:rgba(255,255,255,.7);margin:4px auto 0}
.banner .deal{position:absolute;top:208px;left:0;right:0;font-size:30px}

.wide{position:absolute;left:0;width:1200px;height:536px;color:#fff;text-align:center}
.wide h2{position:absolute;left:0;right:0;font-size:40px;font-weight:400}
.btn-outline{position:absolute;left:525px;width:150px;height:48px;border:2px solid var(--green);border-radius:24px;color:#fff;font-size:16px;display:flex;align-items:center;justify-content:center;background:rgba(0,0,0,.35)}

.blog{position:absolute;top:3546px;left:112px;display:grid;grid-template-columns:repeat(3,308px);column-gap:27px}
.post .img{height:246px}
.post .date{color:var(--green);font-size:15px;margin-top:34px}
.post h4{font-size:16px;font-weight:400;line-height:26px;margin-top:14px}
.post p{font-size:12.5px;color:var(--muted);line-height:26px;margin-top:8px}

.perks{position:absolute;top:4575px;left:0;width:1200px;height:339px}
.perk{position:absolute;top:90px;width:320px;text-align:center}
.perk h4{font-size:22px;font-weight:400;margin-top:18px}
.perk p{font-size:12.5px;color:var(--muted);line-height:26px;margin-top:18px}

.footer{position:absolute;top:4914px;left:0;width:1200px;height:419px;background:var(--footer);color:#fff}
.footer h3{font-size:29px;font-weight:400}
.footer p{font-size:12.5px;line-height:26px;margin-top:16px;color:#ddd}
.links{list-style:none;margin-top:18px;font-size:13px;line-height:30px}
.email{margin-top:18px;width:327px;height:44px;background:#fff;color:#333;font-size:12px;display:flex;align-items:center;padding-left:18px;border-radius:2px}
.submit{margin-top:16px;width:100px;height:34px;background:var(--green);color:#fff;font-size:12px;display:flex;align-items:center;justify-content:center;border-radius:2px}
.divider{position:absolute;top:290px;left:112px;width:976px;height:1px;background:#333}
.cards{position:absolute;top:326px;left:0;right:0;display:flex;justify-content:center;gap:10px}
.cards span{width:38px;height:24px;border-radius:3px;background:#fff;display:block}
.copy{position:absolute;top:374px;left:0;right:0;text-align:center;font-size:13px}
</style>
</head>
<body>
<div class="page">

  <div class="topbar">Free Delivey on all orders over $50</div>

  <header class="nav">
    <nav class="menu">
      <a class="active" href="#">HOME</a><a href="#">ABOUT US</a><a href="#">PRODUCT</a><a href="#">CONTACT US</a>
    </nav>
    <div class="logo">DULTAVO</div>
    <div class="search"><span>SEARCH</span>
      <svg width="15" height="15" viewBox="0 0 16 16"><circle cx="6.5" cy="6.5" r="5" fill="none" stroke="#222" stroke-width="2"/><line x1="10.5" y1="10.5" x2="15" y2="15" stroke="#222" stroke-width="2"/></svg>
    </div>
    <div class="cart"><span class="count">0</span>
      <svg width="18" height="16" viewBox="0 0 18 16"><path d="M0 1h3l2.5 9h9L17 3H4.5" fill="#222"/><circle cx="6.5" cy="13.5" r="1.6" fill="#222"/><circle cx="13.5" cy="13.5" r="1.6" fill="#222"/></svg>CART
    </div>
  </header>

  <section class="hero">
    <div class="panel office" role="img" aria-label="Photo of a tidy office desk with a computer and shelves">
      <div class="caption" style="color:#fff"><small>DULTAVO</small><h3>Office Supplies</h3><a href="#">SHOP NOW</a></div>
    </div>
    <div class="panel offer">
      <div class="art" role="img" aria-label="Illustration of a laptop beside a cup of coloured pencils"></div>
      <div class="lead">FESTIVAL OFFER ON</div>
      <div class="date">OCT 15-30</div>
      <div class="line" style="top:338px">Shop Using KPX&amp;</div>
      <div class="line" style="top:382px">Get up to £100 Cashback*</div>
      <div class="free">
        <svg width="56" height="56" viewBox="0 0 56 56"><circle cx="28" cy="28" r="26" fill="none" stroke="#fff" stroke-width="2"/><rect x="15" y="22" width="18" height="12" fill="none" stroke="#fff" stroke-width="2"/><path d="M33 25h5l4 5v4h-9z" fill="none" stroke="#fff" stroke-width="2"/><circle cx="20" cy="36" r="2.5" fill="#fff"/><circle cx="37" cy="36" r="2.5" fill="#fff"/></svg>
        Free Delivery <span>on your first order</span>
      </div>
      <div class="tiny" style="top:497px">10%Instant Discount*</div>
      <div class="tiny" style="top:526px">On credit/debit Cards &amp; EMI</div>
    </div>
    <div class="panel home" role="img" aria-label="Photo of a couple cooking together in a home kitchen">
      <div class="caption" style="color:#fff"><small>DULTAVO</small><h3>Home Consumables</h3><a href="#">SHOP NOW</a></div>
    </div>
    <div class="arrow" style="left:19px"><svg width="10" height="12" viewBox="0 0 10 12"><path d="M7 1L2 6l5 5" fill="none" stroke="#222" stroke-width="1.6"/></svg></div>
    <div class="arrow" style="left:1145px"><svg width="10" height="12" viewBox="0 0 10 12"><path d="M3 1l5 5-5 5" fill="none" stroke="#222" stroke-width="1.6"/></svg></div>
  </section>

  <h2 class="section-title" style="top:788px">FEATURED PRODUCT</h2>
  <div class="grid" style="top:883px;row-gap:112px">
    <div class="card"><div class="img"><div class="fill" role="img" aria-label="Stationery set with pencils and notebooks" style="background:linear-gradient(135deg,#f0c23a,#e2463f,#3a8fd8)"></div><span class="badge">15% OFF</span></div><div class="stars">★★★★★</div><h4>PRODUCT NAME</h4><div class="price">£45.00</div></div>
    <div class="card"><div class="img"><div class="fill" role="img" aria-label="Rolls of clear packing tape" style="background:linear-gradient(135deg,#e9d9a8,#cdb574)"></div></div><div class="stars">★★★★★</div><h4>PRODUCT NAME</h4><div class="price">£45.00</div></div>
    <div class="card"><div class="img"><div class="fill" role="img" aria-label="Home appliances including fridge and washing machine" style="background:linear-gradient(135deg,#c9cbcd,#6e7174)"></div><span class="badge">15% OFF</span></div><div class="stars">★★★★★</div><h4>PRODUCT NAME</h4><div class="price">£45.00</div></div>
    <div class="card"><div class="img"><div class="fill" role="img" aria-label="Cardboard box filled with office supplies" style="background:linear-gradient(135deg,#b53a34,#c8915a 60%,#3b6fb0)"></div></div><div class="stars">★★★★★</div><h4>PRODUCT NAME</h4><div class="price">£45.00</div></div>
    <div class="card"><div class="img"><div class="fill" role="img" aria-label="Open box of household items" style="background:linear-gradient(135deg,#c9a06c,#9c7446)"></div></div><div class="stars">★★★★★</div><h4>PRODUCT NAME</h4><div class="price">£45.00</div></div>
    <div class="card"><div class="img"><div class="fill" role="img" aria-label="Office laser printer" style="background:linear-gradient(135deg,#e4e4e4,#9a9a9a)"></div><span class="badge">15% OFF</span></div><div class="stars">★★★★★</div><h4>PRODUCT NAME</h4><div class="price">£45.00</div></div>
    <div class="card"><div class="img"><div class="fill" role="img" aria-label="Colourful paper clips" style="background:linear-gradient(135deg,#f4d84a,#4fb1e0 50%,#e0457a)"></div></div><div class="stars">★★★★★</div><h4>PRODUCT NAME</h4><div class="price">£45.00</div></div>
    <div class="card"><div class="img"><div class="fill" role="img" aria-label="Bucket of cleaning products" style="background:linear-gradient(135deg,#2e7fd0,#f0d13a)"></div><span class="badge">15% OFF</span></div><div class="stars">★★★★★</div><h4>PRODUCT NAME</h4><div class="price">£45.00</div></div>
  </div>

  <section class="promo">
    <div class="banner" style="left:112px;background:linear-gradient(135deg,#4a4440,#2c2a28 50%,#6b3e4a)" role="img" aria-label="Photo of pencils, notebooks and sticky notes">
      <div class="label">OFFICE SUPPLIES</div><div class="deal">UP TO 60% OFF</div>
    </div>
    <div class="banner" style="left:614px;background:linear-gradient(135deg,#6d5748,#4a3a30 50%,#7a5a45)" role="img" aria-label="Photo of hands packing a cardboard box">
      <div class="label">PACKING SUPPLIES</div><div class="deal">UP TO 2000 OFF</div>
    </div>
  </section>

  <h2 class="section-title" style="top:2350px">SALE PRODUCT</h2>
  <div class="grid" style="top:2443px">
    <div class="card"><div class="img"><div class="fill" role="img" aria-label="Lever arch files in yellow and blue" style="background:linear-gradient(135deg,#f2c21c,#2f6fd0)"></div><span class="badge">20% OFF</span></div><div class="stars">★★★★★</div><h4>PRODUCT NAME</h4><div class="price">£45.00</div></div>
    <div class="card"><div class="img"><div class="fill" role="img" aria-label="Assorted cleaning bottles" style="background:linear-gradient(135deg,#e4573f,#f2cb38 50%,#46a5dc)"></div></div><div class="stars">★★★★★</div><h4>PRODUCT NAME</h4><div class="price">£45.00</div></div>
    <div class="card"><div class="img"><div class="fill" role="img" aria-label="Cardboard box with tape roll" style="background:linear-gradient(135deg,#c79a63,#9b7142)"></div><span class="badge">15% OFF</span></div><div class="stars">★★★★★</div><h4>PRODUCT NAME</h4><div class="price">£45.00</div></div>
    <div class="card"><div class="img"><div class="fill" role="img" aria-label="Yellow cup of coloured pencils" style="background:linear-gradient(180deg,#e04a3c,#f7d62a 55%)"></div></div><div class="stars">★★★★★</div><h4>PRODUCT NAME</h4><div class="price">£45.00</div></div>
  </div>

  <section class="wide" style="top:2878px;background:linear-gradient(135deg,#5b4a37,#3c3024 45%,#4d4630 70%,#2d2a40)" role="img" aria-label="Photo of sponges, brushes and cleaning bottles">
    <h2 style="top:214px">HOME CONSUMABLES</h2>
    <div class="btn-outline" style="top:278px">SHOP NOW</div>
  </section>

  <h2 class="section-title" style="top:3459px">LATEST BLOG</h2>
  <div class="blog">
    <article class="post"><div class="img" role="img" aria-label="Photo of paper towels in a bright kitchen" style="background:linear-gradient(135deg,#e9e6e0,#bdb6a8)"></div><div class="date">JUNE 29, 2022</div><h4>Sed ut perspiciatis unde omnis iste nat error sit voluptatem</h4><p>Nemo enim ipsam voluptatem quia voluptas sit aspernatur aut odit aut fugit, sed quia consequ untur magni dolores eos qui...</p></article>
    <article class="post"><div class="img" role="img" aria-label="Photo of a box being sealed with a tape dispenser" style="background:linear-gradient(135deg,#d5b88f,#a37d52)"></div><div class="date">JUNE 29, 2022</div><h4>Sed ut perspiciatis unde omnis iste nat error sit voluptatem</h4><p>Nemo enim ipsam voluptatem quia voluptas sit aspernatur aut odit aut fugit, sed quia consequ untur magni dolores eos qui...</p></article>
    <article class="post"><div class="img" role="img" aria-label="Flat lay of stationery on a red desk" style="background:linear-gradient(135deg,#d8434a,#4572c4 55%,#e8e4dc)"></div><div class="date">JUNE 29, 2022</div><h4>Sed ut perspiciatis unde omnis iste nat error sit voluptatem</h4><p>Nemo enim ipsam voluptatem quia voluptas sit aspernatur aut odit aut fugit, sed quia consequ untur magni dolores eos qui...</p></article>
  </div>

  <section class="wide" style="top:4039px;background:linear-gradient(135deg,#3e3229,#5a4636 50%,#2e2620)" role="img" aria-label="Photo of cardboard boxes on a warehouse conveyor">
    <h2 style="top:218px">PACKING SUPPLIES</h2>
    <div class="btn-outline" style="top:288px">SHOP NOW</div>
  </section>

  <section class="perks">
    <div class="perk" style="left:109px">
      <svg width="70" height="80" viewBox="0 0 70 80" fill="none" stroke="#333" stroke-width="2"><path d="M22 16c0-8 26-8 26 0v4H22z"/><circle cx="35" cy="28" r="9"/><path d="M14 68V52c0-7 6-11 12-11h18c6 0 12 4 12 11v16"/><rect x="30" y="52" width="22" height="16"/><line x1="41" y1="52" x2="41" y2="60"/></svg>
      <h4>Free Delivery</h4>
      <p>Sed ut perspiciatis unde omnis iste natus error sit voluptatem accusantium doloremque laudantium, totam rem aperia</p>
    </div>
    <div class="perk" style="left:438px">
      <svg width="90" height="80" viewBox="0 0 90 80" fill="none" stroke="#333" stroke-width="2"><path d="M12 30h56l-10-10M68 30l-10 10"/><path d="M78 50H22l10-10M22 50l10 10"/><path d="M12 30c-6 0-6 20 4 20"/></svg>
      <h4>30-Day Returns</h4>
      <p>Sed ut perspiciatis unde omnis iste natus error sit voluptatem accusantium doloremque laudantium, totam rem aperia</p>
    </div>
    <div class="perk" style="left:765px">
      <svg width="70" height="80" viewBox="0 0 70 80" fill="none" stroke="#333" stroke-width="2"><path d="M35 8l24 8v22c0 16-12 26-24 32C23 64 11 54 11 38V16z"/><path d="M24 38l8 8 14-16"/></svg>
      <h4>Warranty</h4>
      <p>Sed ut perspiciatis unde omnis iste natus error sit voluptatem accusantium doloremque laudantium, totam rem aperia</p>
    </div>
  </section>

  <footer class="footer">
    <div class="abs" style="left:112px;top:50px;width:300px">
      <h3>About Dultavo</h3>
      <p>Sed ut perspiciatis unde omnis iste natus error sit voluptatem accusantium doloremque laudant ium, totam rem aperiam, eaque ipsa quae ab illo inventore dicta sunt explicabo</p>
    </div>
    <div class="abs" style="left:526px;top:50px">
      <h3>Quick links</h3>
      <ul class="links"><li>Home</li><li>About Us</li><li>Product</li><li>Contact us</li></ul>
    </div>
    <div class="abs" style="left:763px;top:50px;width:327px">
      <h3>Newsletter</h3>
      <p>Sed ut perspiciatis unde omnis iste natus error sit voluptatem accusantium doloremque</p>
      <div class="email">Enter Email :</div>
      <div class="submit">SUBMIT</div>
    </div>
    <div class="divider"></div>
    <div class="cards" aria-label="Accepted payment methods"><span></span><span></span><span></span><span></span><span></span><span></span></div>
    <div class="copy">© Copyrights 2022-Dultavo.All Rights Reserved.</div>
  </footer>

</div>
</body>
</html>
```